Steadfast Corner Vending Needs a Promotional Flyer

Design a one page, one sided 8 1/2" x 11" flyer that can be handed out to potential customers. Please keep printing efficiencies in mind. See attached old flyers and company website (steadfastcornervend.example) for reference of services. I have also attached our current logo.

```html
<!DOCTYPE html>
<html lang="en">
<head>
<meta charset="utf-8">
<title>Steadfast Corner Vending Flyer</title>
<link href="https://fonts.googleapis.com/css2?family=Poppins:wght@400;500;600;700;800&display=swap" rel="stylesheet">
<style>
:root{
  --bg:#bdbdbd;
  --paper:#ffffff;
  --navy:#0f2a3d;
  --blue:#0a84f2;
  --blue-dark:#0668c9;
  --red:#e3141b;
  --ink:#111111;
  --text:#2b2b2b;
  --line:#c9d1d8;
}
*{margin:0;padding:0;box-sizing:border-box}
html,body{width:1200px;height:2418px;overflow:hidden;background:var(--bg);font-family:'Poppins',sans-serif}
.flyer{position:absolute;left:50px;top:497px;width:1025px;height:1327px;background:var(--paper);transform:scale(1.073);transform-origin:0 0;box-shadow:0 20px 40px rgba(0,0,0,.25);overflow:hidden}
.abs{position:absolute}
.corner-band{left:664px;top:0;width:361px;height:382px;background:var(--blue);border-bottom-left-radius:70px}
.brand{left:60px;top:88px;display:flex;align-items:center;gap:10px}
.brand-square{width:22px;height:22px;background:var(--blue)}
.brand-name{font-weight:700;font-size:19px;color:var(--navy);line-height:1.1;width:180px}
.welcome{left:58px;top:198px;font-size:42px;font-weight:500;color:var(--ink);letter-spacing:.5px}
.title-main{left:56px;top:246px;font-size:70px;font-weight:800;color:var(--ink);line-height:1}
.title-sub{left:57px;top:318px;font-size:42px;font-weight:700;color:var(--blue);line-height:1}
.badge{left:486px;top:84px;width:132px;height:132px}
.badge-text{left:486px;top:112px;width:132px;text-align:center;color:#fff;line-height:1}
.badge-text small{display:block;font-size:11.5px;font-weight:500}
.badge-text b{display:block;font-size:22px;font-weight:800;margin-top:1px}
.machines{left:600px;top:55px;width:385px;height:327px;background:linear-gradient(90deg,#2a2a2a 0 45%,#d92a1e 47% 100%);border-radius:4px}
.why{left:0;top:382px;width:1025px;height:280px;background:var(--navy);color:#fff}
.why h2{position:absolute;left:58px;top:20px;font-size:27px;font-weight:700}
.why h2 span{color:var(--blue)}
.why-divider{left:514px;top:22px;width:1px;height:240px;background:rgba(255,255,255,.25)}
.why-list{position:absolute;list-style:none;width:440px}
.why-list li{display:flex;align-items:flex-start;gap:12px;font-size:15.5px;line-height:1.17;margin-bottom:16px}
.why-list li svg{flex:none;width:38px;height:38px;margin-top:-4px}
.why-list.left{left:56px;top:70px}
.why-list.right{left:536px;top:70px;width:440px}
.why-list .gap-lg{margin-bottom:24px}
.ph{border-radius:6px}
.svc-bar{height:27px;background:var(--blue);border-radius:0 10px 10px 0;color:#fff;font-size:20px;line-height:27px;padding-left:24px;font-weight:400}
.svc-bar b{font-weight:700}
.svc-body{font-size:13.5px;color:var(--text);line-height:1.25}
.svc-body .q{color:var(--blue);font-weight:600;margin:6px 0 8px}
.svc-body .q2{color:var(--blue);font-weight:600;margin:12px 0 4px}
ul.dots{list-style:none}
ul.dots li{position:relative;padding-left:15px;margin-bottom:6px;font-size:13.5px;line-height:1.2}
ul.dots li::before{content:"";position:absolute;left:0;top:5px;width:7px;height:7px;border-radius:50%;background:var(--blue)}
.cols{display:flex;gap:30px}
.coffee-cols{display:flex;gap:20px}
.coffee-cols ul li{margin-bottom:3px}
.vline{left:512px;top:690px;width:1px;height:440px;background:var(--line)}
.hline{left:58px;top:922px;width:910px;height:1px;background:var(--line)}
.cta{left:58px;top:1155px;width:910px;height:62px;border-radius:12px;overflow:hidden;display:flex}
.cta-left{width:454px;background:var(--navy);padding:7px 0 0 25px;color:#fff;line-height:1.05}
.cta-left .l1{font-size:19px;letter-spacing:5px;font-weight:400}
.cta-left .l2{font-size:20px;color:var(--blue);font-weight:700}
.cta-right{flex:1;background:var(--blue);display:flex;align-items:center;padding-left:40px;color:#fff;font-size:48px;font-weight:800;font-style:italic;letter-spacing:1px}
.cta-phone{left:492px;top:1166px;width:40px;height:40px}
.footer{left:58px;top:1246px;width:910px;display:flex;justify-content:space-between;font-size:18px;color:var(--ink)}
.footer span{display:flex;align-items:center;gap:8px}
</style>
</head>
<body>
<main class="flyer">
  <div class="abs corner-band"></div>

  <div class="abs brand"><div class="brand-square"></div><div class="brand-name">Steadfast Corner Vending</div></div>

  <div class="abs welcome">WELCOME TO</div>
  <div class="abs title-main">STEADFAST</div>
  <div class="abs title-sub">CORNER VENDING</div>

  <svg class="abs badge" viewBox="0 0 100 100" aria-hidden="true">
    <polygon fill="var(--red)" points="50,2 56,12 66,5 69,17 81,14 80,26 92,28 87,39 97,45 88,53 95,63 84,66 87,78 75,78 73,90 62,86 56,97 50,88 44,97 38,86 27,90 25,78 13,78 16,66 5,63 12,53 3,45 13,39 8,28 20,26 19,14 31,17 34,5 44,12"/>
  </svg>
  <div class="abs badge-text"><small>SPECIAL</small><small>PRICING FOR</small><b>BULK</b><b>ORDER</b></div>

  <div class="abs machines ph" role="img" aria-label="Photo of a snack vending machine beside a red cold drink vending machine"></div>

  <section class="abs why">
    <h2>WHY CHOOSE <span>STEADFAST CORNER?</span></h2>
    <div class="abs why-divider"></div>
    <ul class="why-list left">
      <li><svg viewBox="0 0 40 40"><circle cx="20" cy="20" r="18" fill="var(--blue)" stroke="#fff" stroke-width="1.5"/><circle cx="20" cy="21" r="8" fill="none" stroke="#fff" stroke-width="1.6"/><path d="M20 16v5l3 2" stroke="#fff" stroke-width="1.6" fill="none"/></svg><span>Our warehouse is just minutes away so we can get there quickly if a problem should arise.</span></li>
      <li class="gap-lg"><svg viewBox="0 0 40 40"><circle cx="20" cy="20" r="18" fill="var(--blue)" stroke="#fff" stroke-width="1.5"/><circle cx="20" cy="16" r="4" fill="none" stroke="#fff" stroke-width="1.6"/><path d="M12 28c1-5 15-5 16 0" stroke="#fff" stroke-width="1.6" fill="none"/></svg><span>We are a small company that is BIG on service.</span></li>
      <li class="gap-lg"><svg viewBox="0 0 40 40"><circle cx="20" cy="20" r="18" fill="var(--blue)" stroke="#fff" stroke-width="1.5"/><path d="M11 24l9 5 9-5M13 17h14" stroke="#fff" stroke-width="1.6" fill="none"/></svg><span>We are Owner-Operators so we truly CARE about our customers.</span></li>
      <li><svg viewBox="0 0 40 40"><circle cx="20" cy="20" r="18" fill="var(--blue)" stroke="#fff" stroke-width="1.5"/><circle cx="18" cy="18" r="6" fill="none" stroke="#fff" stroke-width="1.6"/><path d="M22 22l6 6" stroke="#fff" stroke-width="1.6"/></svg><span>We are also trained to fix many problems on the spot.</span></li>
    </ul>
    <ul class="why-list right">
      <li class="gap-lg"><svg viewBox="0 0 40 40"><circle cx="20" cy="20" r="18" fill="var(--blue)" stroke="#fff" stroke-width="1.5"/><rect x="14" y="12" width="12" height="16" fill="none" stroke="#fff" stroke-width="1.6"/></svg><span>We will supply machines to your facility.</span></li>
      <li class="gap-lg"><svg viewBox="0 0 40 40"><circle cx="20" cy="20" r="18" fill="var(--blue)" stroke="#fff" stroke-width="1.5"/><path d="M12 22c0-6 16-6 16 0M10 22h20" stroke="#fff" stroke-width="1.6" fill="none"/></svg><span>Customer Service is our priority.</span></li>
      <li class="gap-lg"><svg viewBox="0 0 40 40"><circle cx="20" cy="20" r="18" fill="var(--blue)" stroke="#fff" stroke-width="1.5"/><circle cx="14" cy="17" r="3" fill="#fff"/><circle cx="20" cy="15" r="3" fill="#fff"/><circle cx="26" cy="17" r="3" fill="#fff"/><path d="M10 28h20" stroke="#fff" stroke-width="1.6"/></svg><span>Your employees can choose what types of snacks and drinks they would like to see in the machines.</span></li>
      <li><svg viewBox="0 0 40 40"><circle cx="20" cy="20" r="18" fill="var(--blue)" stroke="#fff" stroke-width="1.5"/><path d="M13 20l5 5 9-10" stroke="#fff" stroke-width="2" fill="none"/></svg><span>We take PRIDE in what we do!</span></li>
    </ul>
  </section>

  <div class="abs vline"></div>
  <div class="abs hline"></div>

  <div class="abs ph" style="left:18px;top:685px;width:127px;height:220px;background:linear-gradient(#3a3f44,#8a949c 50%,#2d3135)" role="img" aria-label="Photo of a glass-front refrigerated drink vending machine"></div>
  <div class="abs svc-bar" style="left:145px;top:688px;width:335px"><b>VENDING MACHINE</b> SERVICES</div>
  <div class="abs svc-body" style="left:170px;top:728px;width:330px">
    <p>Discover Reliability, Convenience, Quality, and Variety . At Zero Cost to You</p>
    <p class="q">Why Choose Our Vending Machine Services?</p>
    <div class="cols">
      <ul class="dots"><li>Zero Cost to you</li><li>Reliability</li><li>Convenience</li><li>Quality</li></ul>
      <ul class="dots"><li>Variety</li><li>Customization</li><li>Technology</li><li>On-time Maintenance</li></ul>
    </div>
  </div>

  <div class="abs ph" style="left:535px;top:685px;width:135px;height:215px;background:linear-gradient(#f4f1ec,#b8885a 45%,#a67a50)" role="img" aria-label="Photo of two paper takeaway coffee cups with lids"></div>
  <div class="abs svc-bar" style="left:640px;top:688px;width:272px;padding-left:42px"><b>COFFEE</b> SERVICE</div>
  <div class="abs svc-body" style="left:685px;top:728px;width:290px">
    <p>we are committed to delivering exceptional coffee and other hot beverage experiences to our customers</p>
    <p class="q2">Our Coffee Selection</p>
    <div class="coffee-cols">
      <ul class="dots" style="width:115px"><li>Harbor Roast</li><li>Morning Mill</li><li>Cedar Bean</li><li>Northbrook Kettle</li></ul>
      <ul class="dots" style="width:125px"><li>Brass Cup</li><li>Ridgeview House</li><li>Other specialty brands upon request</li></ul>
    </div>
  </div>

  <div class="abs ph" style="left:45px;top:940px;width:100px;height:160px;background:linear-gradient(135deg,#1d2a6b,#c9543a 50%,#1d3d9a)" role="img" aria-label="Photo of a blue snack vending machine stocked with chips and candy"></div>
  <div class="abs svc-bar" style="left:145px;top:950px;width:335px"><b>PANTRY</b> SERVICE</div>
  <ul class="abs dots svc-body" style="left:174px;top:988px;width:320px">
    <li>A Snack Time Oasis in Your Workspace</li><li>Tailored to Your Tastes</li><li>Healthy Choices, Happy Teams</li><li>Seamless Restocking and Management</li><li>Flexible and Hassle-Free</li><li>Enhancing Workplace Culture</li>
  </ul>

  <div class="abs ph" style="left:535px;top:945px;width:135px;height:165px;background:linear-gradient(135deg,#1b3f8f,#6b8fc4 50%,#0f2b6a)" role="img" aria-label="Photo of a self-serve micro-market with drink coolers and a payment kiosk"></div>
  <div class="abs svc-bar" style="left:670px;top:950px;width:300px"><b>MICRO-</b>MARKET</div>
  <ul class="abs dots svc-body" style="left:689px;top:988px;width:290px">
    <li>Experience Unmatched Convenience</li><li>Tailored to Your Taste</li><li>Seamless and Secure Transactions</li><li>Freshness Guaranteed</li><li>Smart Inventory Management</li><li>Promoting Workplace Wellbeing</li>
  </ul>

  <div class="abs cta">
    <div class="cta-left"><div class="l1">THERE ARE OTHER SPECIALTY</div><div class="l2">ITEMS AVAILABLE UPON REQUEST</div></div>
    <div class="cta-right">555-014-2730</div>
  </div>
  <svg class="abs cta-phone" viewBox="0 0 40 40" aria-hidden="true"><circle cx="20" cy="20" r="19" fill="#fff"/><path d="M14 11l4 4-2 3c1 3 3 5 6 6l3-2 4 4-3 3c-8 0-15-7-15-15z" fill="var(--blue)"/></svg>

  <div class="abs footer">
    <span><svg width="20" height="20" viewBox="0 0 20 20"><circle cx="10" cy="10" r="8.5" fill="none" stroke="var(--blue)" stroke-width="2"/><path d="M1.5 10h17M10 1.5c-4 4-4 13 0 17M10 1.5c4 4 4 13 0 17" stroke="var(--blue)" stroke-width="1.5" fill="none"/></svg>www.steadfastcornervend.example</span>
    <span><svg width="16" height="20" viewBox="0 0 16 20"><path d="M8 1a6 6 0 0 0-6 6c0 4 6 10 6 10s6-6 6-10a6 6 0 0 0-6-6z" fill="none" stroke="var(--blue)" stroke-width="2"/><circle cx="8" cy="7" r="2" fill="var(--blue)"/></svg>410 Maple Ridge Rd, Unit 12, Fairview, IL 60000</span>
  </div>
</main>
</body>
</html>
```